Brand Identity Stationary Package

Hello I'm looking for a full branding package for my Property Management Company. I have a logo but looking to have the following
Business Card
Email signature
Facebook cover photo
Letterhead (word.doc)
#10 Envelope
Pocket Folder - link to 9x12 pocket folder design specs https://www.printorbit-example.ca/marketing-materials/presentation-folders
would like everything to match and be brand identifiable. The company looks after residential properties/apartments and some commercial properties. Attached is a zip of the files.
For Business Card
Name: Gareth Lindqvist
Position: Operations Manager
Number: 1 (555) 384-2917
Email: Gareth@harborkey-example.ca
Website: Harborkey-example.ca
Property Management

```html
<!DOCTYPE html>
<html lang="en">
<head>
<meta charset="UTF-8">
<title>Harborkey Property Management – #10 Envelope</title>
<link rel="stylesheet" href="https://fonts.googleapis.com/css2?family=Montserrat:wght@500;600&family=Source+Sans+3:wght@400&display=swap">
<style>
  :root {
    --brand-green: #80a641;
    --ink: #111111;
    --paper: #f5f4f4;
    --paper-light: #ffffff;
    --backdrop: #d0cfcf;
  }
  * { margin: 0; padding: 0; box-sizing: border-box; }
  html, body {
    width: 1200px;
    height: 1050px;
    overflow: hidden;
    background: var(--backdrop);
  }
  .canvas {
    position: relative;
    width: 1200px;
    height: 1050px;
  }
  .envelope {
    position: absolute;
    left: 145px;
    width: 910px;
    height: 390px;
    background: radial-gradient(ellipse at 50% 60%, var(--paper-light) 0%, var(--paper) 60%, #efeeee 100%);
    overflow: hidden;
  }
  .envelope--back { top: 105px; }
  .envelope--front { top: 555px; }

  .envelope__art {
    position: absolute;
    inset: 0;
    width: 910px;
    height: 390px;
  }

  .wordmark {
    position: absolute;
    font-family: "Montserrat", sans-serif;
    font-weight: 600;
    line-height: 1;
    white-space: nowrap;
  }
  .tagline {
    position: absolute;
    font-family: "Montserrat", sans-serif;
    font-weight: 500;
    line-height: 1;
    white-space: nowrap;
  }

  .envelope--back .wordmark {
    left: 0; right: 0;
    top: 34px;
    text-align: center;
    font-size: 44px;
    letter-spacing: 5px;
    color: var(--paper-light);
  }
  .envelope--back .tagline {
    left: 0; right: 0;
    top: 79px;
    text-align: center;
    font-size: 10.5px;
    letter-spacing: 8.6px;
    color: var(--paper-light);
  }

  .envelope--front .wordmark {
    left: 52px;
    top: 60px;
    font-size: 40px;
    letter-spacing: 3.5px;
    color: var(--ink);
  }
  .envelope--front .tagline {
    left: 52px;
    top: 101px;
    font-size: 9.5px;
    letter-spacing: 7.2px;
    color: var(--ink);
  }

  .contact-list {
    position: absolute;
    left: 52px;
    top: 148px;
    list-style: none;
    font-family: "Source Sans 3", sans-serif;
    font-size: 20px;
    color: var(--ink);
  }
  .contact-list__item {
    display: flex;
    align-items: center;
    height: 26.5px;
  }
  .contact-list__icon {
    width: 16px;
    height: 16px;
    margin-right: 12px;
    flex: none;
  }
</style>
</head>
<body>
<main class="canvas">

  <section class="envelope envelope--back" aria-label="Envelope back with flap">
    <svg class="envelope__art" viewBox="0 0 910 390" aria-hidden="true">
      <path d="M0 0 H910 L885 90 Q870 131 830 131 H80 Q40 131 25 90 Z" fill="var(--brand-green)"/>
    </svg>
    <div class="wordmark">HARBORKEY</div>
    <div class="tagline">PROPERTY MANAGEMENT</div>
  </section>

  <section class="envelope envelope--front" aria-label="Envelope front">
    <svg class="envelope__art" viewBox="0 0 910 390" aria-hidden="true">
      <path d="M0 219 C120 320 230 345 330 339 C470 332 560 310 680 312 C780 314 860 336 910 359 V390 H0 Z" fill="var(--brand-green)"/>
      <path d="M98 279 C180 320 280 330 420 322 C540 315 640 293 720 298 C790 303 840 320 871 333 C830 322 780 309 720 307 C630 302 540 322 420 332 C270 340 170 320 98 279 Z" fill="var(--ink)"/>
    </svg>

    <div class="wordmark">HARBORKEY</div>
    <div class="tagline">PROPERTY MANAGEMENT</div>

    <ul class="contact-list">
      <li class="contact-list__item">
        <svg class="contact-list__icon" viewBox="0 0 16 16" aria-hidden="true">
          <path d="M1 6 Q8 1 15 6 L13 8 L11 6.5 L5 6.5 L3 8 Z" fill="var(--brand-green)"/>
          <rect x="3" y="8" width="10" height="6" rx="1" fill="var(--brand-green)"/>
          <circle cx="8" cy="11" r="1.6" fill="var(--paper)"/>
        </svg>
        <span>1 (555) 384-2917</span>
      </li>
      <li class="contact-list__item">
        <svg class="contact-list__icon" viewBox="0 0 16 16" aria-hidden="true">
          <rect x="0.5" y="3" width="15" height="10" fill="var(--brand-green)"/>
          <path d="M0.5 3.5 L8 9 L15.5 3.5 M0.5 13 L6 8 M15.5 13 L10 8" stroke="var(--paper)" stroke-width="1.2" fill="none"/>
        </svg>
        <span>Gareth@harborkey-example.ca</span>
      </li>
      <li class="contact-list__item">
        <svg class="contact-list__icon" viewBox="0 0 16 16" aria-hidden="true">
          <circle cx="8" cy="8" r="7.5" fill="var(--brand-green)"/>
          <path d="M4 4 Q7 3 7 6 Q5 8 3.5 7 Z M9 9 Q12 8 12 11 Q10 13 9 12 Z M10 3 Q12 3 13 5 Q11 5 10 3 Z" fill="var(--paper)"/>
        </svg>
        <span>www.Harborkey-example.ca</span>
      </li>
    </ul>
  </section>

</main>
</body>
</html>
```